Velvet Pressings Techno Label Business Card

I'm looking for a very clean business card for my Velvet Pressings music label. The label focusses on techno music. The card should include:

• my name : Tomas Brandt as "Founder & CEO"
• email address: tomas@velvet-pressings.example
• web: www.velvet-pressings.example
• facebook logo + /velvetpress
• twitter logo + /velvetpress
• soundcloud logo + /velvetpressings

Feel free to include your ideas! I'm looking forward to discuss about it.

Tomas

Industry/Entity Type

Business

Contact Information for Business Card

I don't like glossy cards. Prefer matt.

Requirements
Nice to have
• Maybe on one side the complete logo, other side just the icon.
Should not have
• Flashy stuff. Must be clean and business like style.

```html
<!DOCTYPE html>
<html lang="en">
<head>
<meta charset="UTF-8">
<title>Velvet Pressings – Business Card</title>
<link rel="stylesheet" href="https://fonts.googleapis.com/css2?family=Exo+2:wght@400;500;600;700&display=swap">
<style>
  :root {
    --bg: #e9e7e4;
    --card-top: #ffffff;
    --card-bottom: #ececec;
    --band: #7d7d7d;
    --orange: #ff6a00;
    --ink: #333333;
    --grey-text: #6e6e6e;
    --white: #ffffff;
  }
  * { margin: 0; padding: 0; box-sizing: border-box; }
  html, body {
    width: 1200px; height: 900px; overflow: hidden;
    background: var(--bg);
    font-family: "Exo 2", sans-serif;
  }
  .stage {
    width: 1200px; height: 900px;
    display: flex; align-items: center; justify-content: center;
  }
  .card {
    position: relative;
    width: 910px; height: 520px;
    background: linear-gradient(180deg, var(--card-top) 0%, var(--card-bottom) 100%);
    box-shadow: 0 10px 30px rgba(0,0,0,0.18);
    overflow: hidden;
  }
  .card__waves { position: absolute; inset: 0; width: 910px; height: 520px; }
  .brand__dot {
    position: absolute; left: 470px; top: 52px;
    width: 66px; height: 66px; border-radius: 50%;
    background: var(--orange);
  }
  .brand__name {
    position: absolute; left: 200px; top: 128px;
    font-size: 54px; font-weight: 600;
    color: var(--grey-text);
    letter-spacing: -0.5px; line-height: 1; white-space: nowrap;
  }
  .person {
    position: absolute; right: 58px; top: 196px; text-align: right;
  }
  .person__name {
    font-size: 24px; font-weight: 500; color: var(--orange);
    letter-spacing: 2px; text-transform: uppercase; line-height: 1.2;
  }
  .person__title {
    font-size: 19px; font-weight: 500; color: var(--ink); margin-top: 2px;
  }
  .address {
    position: absolute; right: 38px; top: 340px; text-align: right;
    font-style: normal;
    color: var(--white); font-size: 18px; line-height: 1.35; letter-spacing: 0.5px;
  }
  .contacts {
    position: absolute; left: 52px; top: 386px;
    list-style: none; color: var(--white);
    font-size: 16px; letter-spacing: 0.6px;
  }
  .contacts__item { display: flex; align-items: center; height: 21px; }
  .contacts__icon { width: 14px; height: 14px; margin-right: 12px; flex: none; }
</style>
</head>
<body>
<main class="stage">
  <section class="card" aria-label="Velvet Pressings business card">
    <svg class="card__waves" viewBox="0 0 910 520" aria-hidden="true">
      <path d="M0,372 C210,350 420,430 620,365 C760,318 850,300 910,290 L910,520 L0,520 Z" fill="var(--band)"/>
      <path d="M0,360 C210,335 420,410 620,348 C760,302 850,282 910,270 L910,282 C850,294 760,316 625,362 C420,428 210,352 0,374 Z" fill="var(--orange)"/>
      <path d="M0,340 C220,318 430,392 630,330 C760,290 850,265 910,250" fill="none" stroke="var(--orange)" stroke-width="3"/>
    </svg>

    <span class="brand__dot"></span>
    <span class="brand__name">Velvet Pressings</span>

    <div class="person">
      <p class="person__name">Tomas Brandt</p>
      <p class="person__title">Founder &amp; CEO</p>
    </div>

    <address class="address">
      041, 6th floor, Quay<br>Harbour Lane DKM
    </address>

    <ul class="contacts">
      <li class="contacts__item">
        <svg class="contacts__icon" viewBox="0 0 16 16"><path d="M3 1h3l1.5 4-2 1.2a9 9 0 0 0 4.3 4.3L11 8.5l4 1.5v3a2 2 0 0 1-2 2C7 15 1 9 1 3a2 2 0 0 1 2-2z" fill="var(--orange)"/></svg>
        020 555 0142
      </li>
      <li class="contacts__item">
        <svg class="contacts__icon" viewBox="0 0 16 16"><circle cx="8" cy="8" r="6" fill="var(--orange)"/></svg>
        /velvetpress
      </li>
      <li class="contacts__item">
        <svg class="contacts__icon" viewBox="0 0 16 16"><circle cx="8" cy="8" r="6" fill="var(--orange)"/></svg>
        /velvetpress
      </li>
      <li class="contacts__item">
        <svg class="contacts__icon" viewBox="0 0 16 16"><circle cx="8" cy="8" r="6" fill="var(--orange)"/></svg>
        /velvetpressings
      </li>
      <li class="contacts__item">
        <svg class="contacts__icon" viewBox="0 0 16 16"><rect x="1" y="3" width="14" height="10" rx="1" fill="var(--orange)"/><path d="M1.5 4 8 9l6.5-5" fill="none" stroke="var(--band)" stroke-width="1.4"/></svg>
        tomas@velvet-pressings.example
      </li>
      <li class="contacts__item">
        <svg class="contacts__icon" viewBox="0 0 16 16"><circle cx="8" cy="8" r="7" fill="var(--orange)"/><path d="M1 8h14M8 1c-3 4-3 10 0 14M8 1c3 4 3 10 0 14" fill="none" stroke="var(--band)" stroke-width="1"/></svg>
        www.velvet-pressings.example
      </li>
    </ul>
  </section>
</main>
</body>
</html>
```